Custom unique Stationary design for Logistics company

We need a custom, unique , elegant and luxurious full stationary design using our new logo, following these guidelines:
1- Business card: double sided, both sides uses the navy blue as the background main color (same as the code of the navy blue used in our logo).
2- envelope and folder: also use the same navy blue as the main background color.
3- book cover( notepad cover) : same thing with the navy blue
4- letterhead: feel free to use the combination of the colors in our logo.
5- rest of the items are up to your creativity

Target Market(s)

corporates and other businesses

Industry/Entity Type

Logistics and heavy machines contractors

Requirements
Must have
• Letterhead, business card, envelope, notepad cover, paper, file
Nice to have
• navy blue to be main background color for business card, envelope, notepad cover

```html
<!DOCTYPE html>
<html lang="en">
<head>
<meta charset="utf-8">
<title>Harborline Freight Group — Business Card</title>
<link rel="stylesheet" href="https://fonts.googleapis.com/css2?family=Michroma&family=Montserrat:wght@400;500;600&display=swap">
<style>
  :root {
    --navy: #03426b;
    --navy-deep: #023559;
    --orange: #f15a24;
    --white: #ffffff;
    --stage: #d6d6d6;
  }
  html, body {
    margin: 0;
    padding: 0;
    width: 1200px;
    height: 800px;
    overflow: hidden;
    background: var(--stage);
  }
  .canvas {
    position: relative;
    width: 1200px;
    height: 800px;
    display: flex;
    align-items: center;
    justify-content: center;
    gap: 60px;
  }
  .card {
    position: relative;
    width: 525px;
    height: 300px;
    border-radius: 18px;
    background: linear-gradient(135deg, var(--navy) 0%, var(--navy-deep) 100%);
    box-shadow: 0 10px 24px rgba(0,0,0,0.25);
    overflow: hidden;
    font-family: "Montserrat", sans-serif;
    color: var(--white);
  }

  /* Contact side */
  .holder {
    position: absolute;
    right: 245px;
    top: 172px;
    text-align: right;
  }
  .holder-name {
    font-family: "Michroma", sans-serif;
    font-weight: 400;
    font-size: 17px;
    letter-spacing: 0.5px;
    margin: 0;
    line-height: 1.1;
    white-space: nowrap;
  }
  .holder-role {
    color: var(--orange);
    font-size: 12px;
    letter-spacing: 1.5px;
    margin: 4px 0 0;
  }
  .divider {
    position: absolute;
    left: 298px;
    top: 118px;
    width: 1px;
    height: 100px;
    background: var(--orange);
  }
  .contact-list {
    position: absolute;
    left: 316px;
    top: 98px;
    margin: 0;
    padding: 0;
    list-style: none;
    font-size: 12px;
    line-height: 1.3;
  }
  .contact-list li {
    display: flex;
    align-items: flex-start;
    gap: 8px;
    margin-bottom: 2px;
    white-space: nowrap;
  }
  .contact-list svg {
    flex: none;
    width: 11px;
    height: 11px;
    margin-top: 3px;
    fill: var(--orange);
  }
  .web {
    position: absolute;
    left: 316px;
    top: 252px;
    margin: 0;
    font-size: 11px;
    letter-spacing: 3px;
    white-space: nowrap;
  }

  /* Brand side */
  .brand {
    position: absolute;
    inset: 0;
    display: flex;
    align-items: center;
    justify-content: center;
    gap: 12px;
  }
  .brand-mark {
    width: 14px;
    height: 14px;
    background: var(--orange);
  }
  .brand-name {
    font-family: "Montserrat", sans-serif;
    font-weight: 600;
    font-size: 28px;
    letter-spacing: 1px;
    color: var(--white);
  }
</style>
</head>
<body>
<main class="canvas">

  <section class="card card-contact" aria-label="Business card, contact side">
    <div class="holder">
      <h1 class="holder-name">DANIEL MERCER</h1>
      <p class="holder-role">President</p>
    </div>

    <div class="divider"></div>

    <ul class="contact-list">
      <li>
        <svg viewBox="0 0 12 12" aria-hidden="true"><path d="M6 0a4 4 0 0 0-4 4c0 3 4 8 4 8s4-5 4-8a4 4 0 0 0-4-4zm0 5.5A1.5 1.5 0 1 1 6 2.5a1.5 1.5 0 0 1 0 3z"/></svg>
        <span>4210 Birchwood Drive<br>Fairview, Oregon 97024</span>
      </li>
      <li>
        <svg viewBox="0 0 12 12" aria-hidden="true"><path d="M2.5 0.5l2 2-1 1.5a7 7 0 0 0 4.5 4.5l1.5-1 2 2-1.5 2C5 11 1 7 0.5 2z"/></svg>
        <span>555-204-7731</span>
      </li>
      <li>
        <svg viewBox="0 0 12 12" aria-hidden="true"><path d="M3 0h6v12H3zM4 1v9h4V1z"/></svg>
        <span>555-318-6642</span>
      </li>
      <li>
        <svg viewBox="0 0 12 12" aria-hidden="true"><path d="M0 2h12v8H0zm1 1v.5l5 3 5-3V3z"/></svg>
        <span>daniel@harborline.com</span>
      </li>
    </ul>

    <p class="web">www.harborline.com</p>
  </section>

  <section class="card card-brand" aria-label="Business card, brand side">
    <div class="brand">
      <span class="brand-mark" aria-hidden="true"></span>
      <span class="brand-name">Harborline Freight Group</span>
    </div>
  </section>

</main>
</body>
</html>
```